Webdesign für Steuerberaterin
Zielgruppe
Ich bin Steuerberaterin. Meine Zielgruppe sind sowohl Privatpersonen als auch Unternehmer sowie Männer und Frauen.
Aufgabenstellung
Bitte mein Logo und Foto mit berücksichtigen. Ich möchte keine Website, auf der alle 'Reiter' als eine Seite von oben nach unten durchlaufen. Sondern wirklich einzelne, voneinander getrennte Seiten.

```html
<!DOCTYPE html>
<html lang="de">
<head>
<meta charset="utf-8">
<title>Maren Brodtke – Steuerberaterin</title>
<link href="https://fonts.googleapis.com/css2?family=Gelasio&family=PT+Sans:wght@400;700&display=swap" rel="stylesheet">
<style>
  :root {
    --header-dark: #1c1a1f;
    --gold: #b38a2c;
    --gold-band: #dab83c;
    --text: #4b4a4d;
    --rule: #3a3a3a;
    --white: #ffffff;
  }
  * { margin: 0; padding: 0; box-sizing: border-box; }
  html, body { width: 1200px; height: 1104px; overflow: hidden; background: var(--white); }
  .page { position: relative; width: 1200px; height: 1104px; overflow: hidden; font-family: "PT Sans", sans-serif; color: var(--text); }

  .site-header { position: absolute; left: 0; top: 0; width: 1200px; height: 272px; background: var(--header-dark); }
  .brand {
    position: absolute; left: 542px; top: 0; width: 183px; height: 179px;
    background: var(--white); display: flex; align-items: center; justify-content: center; gap: 8px;
  }
  .brand-dot { width: 10px; height: 10px; border-radius: 50%; background: var(--gold); }
  .brand-name { font-family: "PT Sans", sans-serif; font-size: 19px; font-weight: 400; color: var(--gold); }

  .main-nav a {
    position: absolute; top: 242px; font-size: 13.5px; color: var(--gold); text-decoration: none; line-height: 20px;
  }
  .nav-about { left: 193px; }
  .nav-services { left: 285px; }
  .nav-contact { left: 880px; }
  .nav-imprint { left: 967px; }

  .portrait {
    position: absolute; left: 376px; top: 265px; width: 477px; height: 327px;
    background: radial-gradient(ellipse at 50% 45%, #f7f7f7 0%, #dedede 55%, #b9b9b9 100%);
  }
  .portrait-figure {
    position: absolute; left: 50%; bottom: 0; transform: translateX(-50%);
    width: 220px; height: 190px; border-radius: 90px 90px 0 0; background: #1d2030;
  }

  .welcome-title {
    position: absolute; left: 377px; top: 629px; width: 477px; display: flex; align-items: center; gap: 13px;
  }
  .welcome-title::before, .welcome-title::after { content: ""; flex: 1; height: 1px; background: var(--rule); }
  .welcome-title h1 { font-family: "Gelasio", serif; font-weight: 400; font-size: 24px; color: var(--gold); white-space: nowrap; }

  .intro { position: absolute; left: 0; width: 1200px; text-align: center; font-size: 16px; line-height: 21.7px; }
  .intro-lead { top: 697px; font-weight: 700; font-size: 16.5px; }
  .intro-p1 { top: 734px; }
  .intro-p2 { top: 866px; }
  .intro-p3 { top: 933px; }

  .footer-band { position: absolute; left: 0; top: 1078px; width: 1200px; height: 26px; background: var(--gold-band); }
</style>
</head>
<body>
<div class="page">
  <header class="site-header">
    <div class="brand"><span class="brand-dot"></span><span class="brand-name">Maren Brodtke</span></div>
    <nav class="main-nav">
      <a class="nav-about" href="#">Über mich</a>
      <a class="nav-services" href="#">Leistungen</a>
      <a class="nav-contact" href="#">Kontakt</a>
      <a class="nav-imprint" href="#">Impressum</a>
    </nav>
  </header>

  <div class="portrait" role="img" aria-label="Porträtfoto der Steuerberaterin im dunklen Blazer vor heller Steinwand">
    <div class="portrait-figure"></div>
  </div>

  <div class="welcome-title"><h1>Schön, dass Sie da sind</h1></div>

  <p class="intro intro-lead">Ich freue mich, dass Sie den Weg zu mir gefunden haben!</p>
  <p class="intro intro-p1">Sie sind bei mir genau richtig:<br>Egal, ob Sie Privatperson sind, die Ihre Einkommensteuer-Erklärung<br>in vertrauensvolle Hände geben möchte,<br>oder Unternehmer, der sich z.B. das „Rundum-Sorglos-Paket“<br>mit Buchführung, Jahresabschluss und Steuererklärungen wünscht.</p>
  <p class="intro intro-p2">Schauen Sie sich hier gerne um und melden Sie sich bei mir - ich bin bei jedem<br>steuerlichen Thema gerne Ihr kompetenter und zuverlässiger Ansprechpartner.</p>
  <p class="intro intro-p3">Für mich ist es eine Selbstverständlichkeit,<br>dass ich auch nach mehr als 12 Jahren Berufserfahrung<br>durch permanente Fortbildungen immer auf dem aktuellsten Stand<br>der relevanten Gesetze und Verordnungen bin.<br>Nur so kann ich Sie bestmöglich beraten.</p>

  <div class="footer-band"></div>
</div>
</body>
</html>
```